Letterhead for a German Distribution/Manufacturing Company

We need a professional Letterhead in a unique Design.
not to playful.
The Letterhead has to show show that we are a international company with headquater in Germany.
all details like adress, Vat Tax Number, Bank Accout, Eori, email, Company number has to be on the Letterhead.
for example use: VAT TAX DE5470318 Bank Account: Kestrel Bank IBAN DE412058731ß204683 Swift: MORV0417352 EORI 3150428697 Company Number: HRB 51806 Adress: VOLMINTA UG Ahornweg 7 Postal Code 06384 City Lindenfeld Country: Germany Email: info@volminta-example.com
the design can be colored but doesnt have to be
Industry/Entity Type
Manufacturing and international distribution
Requirements
Must have
- show that we are a international company with headquater in Germany. our company infos and logo

```html
<!DOCTYPE html>
<html lang="en">
<head>
<meta charset="utf-8">
<title>VOLMINTA Stationery</title>
<link href="https://fonts.googleapis.com/css2?family=Roboto:wght@400&display=swap" rel="stylesheet">
<style>
  :root {
    --backdrop: #5f5f6c;
    --paper: #ececee;
    --ink: #3a3a3d;
    --ink-soft: #55555a;
    --flap: #363638;
    --mark-faint: rgba(0,0,0,0.07);
    --mark-light: #d8d8da;
    --fold: #d6d6d8;
  }
  * { margin: 0; padding: 0; box-sizing: border-box; }
  html, body { width: 1200px; height: 830px; overflow: hidden; }
  body {
    background: var(--backdrop);
    font-family: "Roboto", Arial, sans-serif;
    color: var(--ink);
    position: relative;
  }
  address { font-style: normal; }
  .brand {
    position: absolute;
    display: flex; align-items: center; gap: 7px;
    font-weight: 400; color: var(--ink); letter-spacing: 0.02em; line-height: 1;
  }
  .brand-dot { border-radius: 50%; background: var(--ink); flex: none; }
  .flap-dot {
    position: absolute; width: 44px; height: 44px; border-radius: 50%;
    background: var(--mark-light);
  }

  /* Envelope front */
  .envelope-front {
    position: absolute; left: 201px; top: 145px; width: 416px; height: 290px;
  }
  .envelope-front .flap {
    position: relative; height: 83px; background: var(--flap);
    border-radius: 14px 14px 0 0;
  }
  .envelope-front .flap-dot { left: 186px; top: 16px; }
  .envelope-front .face {
    position: relative; height: 207px; background: var(--paper); overflow: hidden;
  }
  .envelope-front .watermark {
    position: absolute; left: 263px; top: -11px;
    width: 200px; height: 200px; border-radius: 50%; background: var(--mark-faint);
  }
  .envelope-front .brand { left: 25px; top: 32px; font-size: 15px; }
  .envelope-front .brand-dot { width: 15px; height: 15px; }
  .envelope-front .sender {
    position: absolute; left: 25px; top: 158px;
    font-size: 6.8px; line-height: 8.3px; color: var(--ink-soft);
  }

  /* Envelope back */
  .envelope-back {
    position: absolute; left: 200px; top: 471px; width: 414px; height: 208px;
    background: var(--paper);
  }
  .envelope-back svg { position: absolute; left: 0; top: 0; }
  .envelope-back .flap-dot { left: 185px; top: 18px; }

  /* Letterhead */
  .letterhead {
    position: absolute; left: 661px; top: 157px; width: 402px; height: 533px;
    background: var(--paper); overflow: hidden;
  }
  .letterhead .watermark {
    position: absolute; left: 115px; top: 145px;
    width: 210px; height: 210px; border-radius: 50%; background: var(--mark-faint);
  }
  .letterhead .brand { left: 40px; top: 38px; font-size: 18px; }
  .letterhead .brand-dot { width: 17px; height: 17px; }
  .company-data {
    position: absolute; right: 41px; top: 29px; text-align: right;
    font-size: 5.8px; line-height: 8.2px; color: var(--ink-soft);
  }
  .contact {
    position: absolute; left: 43px; top: 481px; list-style: none;
    font-size: 6.5px; line-height: 8.2px; color: var(--ink-soft);
  }
  .contact li { display: flex; align-items: center; gap: 4px; }
  .contact svg { width: 6px; height: 6px; fill: var(--ink-soft); flex: none; }
  .address {
    position: absolute; right: 41px; top: 481px; text-align: right;
    font-size: 6.5px; line-height: 8.2px; color: var(--ink-soft);
  }
</style>
</head>
<body>

  <section class="envelope-front">
    <div class="flap"><div class="flap-dot"></div></div>
    <div class="face">
      <div class="watermark"></div>
      <div class="brand"><span class="brand-dot"></span>VOLMINTA</div>
      <address class="sender">
        VOLMINTA UG<br>Ahornweg 7 06384<br>City Lindenfeld Germany
      </address>
    </div>
  </section>

  <section class="envelope-back">
    <svg viewBox="0 0 414 208" width="414" height="208">
      <line x1="2" y1="208" x2="40" y2="84" stroke="var(--fold)" stroke-width="1"/>
      <line x1="412" y1="208" x2="374" y2="84" stroke="var(--fold)" stroke-width="1"/>
      <path d="M0 0 H414 L384 74 Q378 85 366 85 H48 Q36 85 30 74 Z" fill="var(--flap)"/>
    </svg>
    <div class="flap-dot"></div>
  </section>

  <section class="letterhead">
    <div class="watermark"></div>
    <div class="brand"><span class="brand-dot"></span>VOLMINTA</div>
    <div class="company-data">
      VAT TAX DE5470318<br>
      Bank Account: Kestrel Bank IBAN DE412058731ß204683<br>
      Swift: MORV0417352 EORI 3150428697<br>
      Company Number: HRB 51806
    </div>
    <ul class="contact">
      <li><svg viewBox="0 0 10 10"><path d="M2 0h2l1 3-1.5 1a6 6 0 0 0 2.5 2.5L7 5l3 1v2a2 2 0 0 1-2 2A8 8 0 0 1 0 2a2 2 0 0 1 2-2z"/></svg>555.013.4827</li>
      <li><svg viewBox="0 0 10 10"><path d="M0 2h10v6H0z"/></svg>info@volminta-example.com</li>
      <li><svg viewBox="0 0 10 10"><circle cx="5" cy="5" r="5"/></svg>www.volminta-example.com</li>
    </ul>
    <address class="address">
      VOLMINTA UG<br>Ahornweg 7 06384<br>City Lindenfeld Germany
    </address>
  </section>

</body>
</html>
```